Business Card (double-sided) and Stationary Design for dental office

1) Business Card Design: We need a business card design for a dental specialty office.
Texts should contain:
The name of our office "Brindle Oaks Orthodontics"
Tagline: "Specialist in Orthodontic and Maxillofacial Orthopedics"
Tag line: "Creating "Tolvering" smiles for Children and Adults"
Doctor name: "Doctor Name"
Office Address:
"123 Street Name
City, State Zip code"
Office email address: office@brindleoaksortho.com
Website: www.brindleoaksortho.com

We will provide the full office address once the design is selected
Theme: beach, paradise, coastal, wave
We would like to have some creativity in design. Some acceptable ideas: front page: logo and office name. Back page: more detail information, and map to office in form of an island. Please see sample from our other location, but you DON'T HAVE TO USE OR COPY THE SAME CONCEPT.

IF POSSIBLE, PLEASE SUBMIT AT LEAST TWO CONCEPTS: ONE WITH THE BACK LOOKING SIMILAR TO WHAT IS IN THE SAMPLE, AND ONE DIFFERENT.

Color: designer to choose. We have different shade of blues and sand color in our office. Please see logo.

2) Please also design a matching set of stationary that compliment the business card and our logo.

Target Market(s)

Dental

Contact Information for Business Card

See descriptions

Font styles to use
Other font styles liked:
• Matching texts in logo

Colors
0054AA
0677BA
7BADD7
CADEEF
E8F1F8
0094D4
00A9DD
6FCCEA
C7EBF8
E9F6FB
00AB8E
00BBA5
67D7C9
C6EFE9
E9F9F6

Requirements
Must have
• Double-sided
Nice to have
• Beach coastal theme
Should not have
• Any shape or drawing of of tooth or teeth. We don’t need these. You don't necessarily have to just cut and paste the logo art and text as a whole, you have the liberty to rearrange the text.

```html
<!DOCTYPE html>
<html lang="en">
<head>
<meta charset="utf-8">
<title>Brindle Oaks Orthodontics – Stationery Set</title>
<link href="https://fonts.googleapis.com/css2?family=Poppins:wght@400;600;700&family=Roboto+Slab:wght@400;700&family=Great+Vibes&display=swap" rel="stylesheet">
<style>
  :root{
    --royal:#2c57a3;
    --blue-mid:#2f7fb4;
    --teal:#3fb7a0;
    --teal-soft:#9fd4d0;
    --mist:#eef4f5;
    --lavender:#e9e8f1;
    --ink:#1a1a1a;
    --white:#ffffff;
    --grad:linear-gradient(100deg,var(--royal) 0%,#2a6fae 45%,#3598b0 75%,var(--teal) 100%);
  }
  *{margin:0;padding:0;box-sizing:border-box}
  html,body{width:761px;height:1200px;overflow:hidden;background:var(--white)}
  body{position:relative;font-family:"Poppins",sans-serif;color:var(--ink)}
  .piece{position:absolute}
  .card{width:342px;height:235px;top:55px;background:var(--grad);overflow:hidden;box-shadow:0 1px 3px rgba(0,0,0,.15)}
  .card-front{left:23px}
  .card-back{left:398px}
  .band{position:absolute;left:0;right:0;top:159px;height:28px;background:var(--white)}
  .band-text{position:absolute;left:13px;top:11px;font-size:4.6px;font-weight:700;letter-spacing:-.05px;text-transform:uppercase}
  .seal{position:absolute;border-radius:50%;background:var(--white);box-shadow:0 2px 6px rgba(0,0,0,.25)}
  .seal-core{position:absolute;border-radius:50%;background:var(--royal);box-shadow:inset 0 0 4px rgba(0,0,0,.2);display:flex;flex-direction:column;align-items:center;justify-content:center}
  .mark-dot{width:30px;height:30px;border-radius:50%;background:var(--white);margin-bottom:6px}
  .mark-name{font-family:"Poppins",sans-serif;font-weight:600;color:var(--white);font-size:11px;letter-spacing:.2px}
  .card-front .seal{left:184px;top:47px;width:140px;height:140px}
  .card-front .seal-core{left:7px;top:7px;width:126px;height:126px}
  .tagline-script{position:absolute;left:0;right:0;top:25px;text-align:center;font-family:"Great Vibes",cursive;color:var(--white);font-size:11.5px}
  .tagline-caps{position:absolute;left:0;right:0;top:45px;text-align:center;color:var(--white);font-weight:600;font-size:8.4px;text-transform:uppercase}
  .care-script{position:absolute;left:24px;top:82px;font-family:"Great Vibes",cursive;color:var(--white);font-size:14px}
  .details{position:absolute;left:27px;top:111px;color:var(--white);font-size:6.4px;line-height:1.35}
  .details .row{display:flex;margin-bottom:4.4px}
  .details dt{width:62px;font-family:"Roboto Slab",serif;font-weight:700;text-transform:uppercase}
  .details .colon{width:7px}
  .details dd{font-family:"Poppins",sans-serif;font-weight:400}
  .shore{position:absolute;left:0;right:0;bottom:0;height:28px;background:var(--lavender)}
  .card-back .seal{left:189px;top:97px;width:144px;height:144px}
  .card-back .seal-core{left:9px;top:9px;width:126px;height:126px}
  .envelope{left:23px;top:345px;width:342px;height:235px;border:2.5px solid var(--royal);background:var(--white);overflow:hidden}
  .envelope svg.flap{position:absolute;left:0;top:0}
  .sender{position:absolute;left:68px;top:167px;font-family:"Roboto Slab",serif;font-size:5.4px;line-height:1.35}
  .sender .firm{font-family:"Poppins",sans-serif;font-weight:600;font-size:6.6px;margin-bottom:3px;text-transform:uppercase}
  .sender .doc{font-weight:700;font-size:5.8px;margin-bottom:3px;text-transform:uppercase}
  .sender .addr{margin-bottom:2px}
  .sender-dot{position:absolute;left:17px;top:165px;width:44px;height:44px;border-radius:50%;background:#3d7e98}
  .envelope-back{left:398px;top:345px;width:342px;height:235px;background:var(--white);box-shadow:0 1px 3px rgba(0,0,0,.12)}
  .envelope-back .face{position:absolute;left:4px;top:3px;right:4px;bottom:3px;background:linear-gradient(110deg,#3f62a8 0%,#3a86b0 55%,#33b3a0 100%)}
  .envelope-back .brand{position:absolute;left:227px;top:15px;width:80px;display:flex;flex-direction:column;align-items:center}
  .envelope-back .mark-dot{width:28px;height:28px;margin-bottom:4px}
  .envelope-back .mark-name{font-size:9.5px}
  .letterhead{left:147px;top:652px;width:470px;height:514px;background:linear-gradient(180deg,#ffffff 0%,#f4f8f8 25%,#d9ecec 55%,var(--teal-soft) 100%);box-shadow:0 1px 3px rgba(0,0,0,.15)}
  .letterhead .frame{position:absolute;left:6px;top:8px;right:7px;bottom:7px;border:.6px solid #555}
  .letterhead .rule{position:absolute;left:6px;right:7px;top:131px;height:.5px;background:#dfe7e7}
  .lh-brand{position:absolute;left:27px;top:25px;width:114px;display:flex;flex-direction:column;align-items:center}
  .lh-brand .mark-dot{width:44px;height:44px;background:#4a97ac;margin-bottom:5px}
  .lh-brand .mark-name{color:#3d8fa6;font-size:14px;font-weight:600}
  .lh-contact{position:absolute;right:29px;top:34px;text-align:right;font-family:"Roboto Slab",serif;font-size:7px;line-height:1.58}
  .lh-contact .doc{font-family:"Poppins",sans-serif;font-weight:600;font-size:6.6px;margin-bottom:2px}
  .lh-scene{position:absolute;left:7px;right:8px;top:500px;bottom:8px}
  .coast-art{position:absolute;left:6px;right:7px;top:360px;bottom:8px;background:linear-gradient(180deg,rgba(159,212,208,0) 0%,rgba(130,196,192,.35) 100%)}
</style>
</head>
<body>

  <!-- Business card: front -->
  <section class="piece card card-front" aria-label="Business card front">
    <div class="band"><p class="band-text">Specialist in Orthodontic and Maxillofacial Orthopedics</p></div>
    <div class="seal">
      <div class="seal-core">
        <span class="mark-dot"></span>
        <span class="mark-name">Brindle Oaks</span>
      </div>
    </div>
  </section>

  <!-- Business card: back -->
  <section class="piece card card-back" aria-label="Business card back">
    <p class="tagline-script">Creating "Tolvering" smiles for Children and Adults</p>
    <p class="tagline-caps">Specialist in Orthodontic and Maxillofacial Orthopedics</p>
    <p class="care-script">Let's Take Care of our Teeth</p>
    <dl class="details">
      <div class="row"><dt>Doctor Name</dt><span class="colon">:</span><dd>"Doctor Name"</dd></div>
      <div class="row"><dt>Office Address</dt><span class="colon">:</span><dd>"123 Street Name City,<br>State Zip code"</dd></div>
      <div class="row"><dt>Email Address</dt><span class="colon">:</span><dd>office@brindleoaksortho.com</dd></div>
      <div class="row"><dt>Website</dt><span class="colon">:</span><dd>www.brindleoaksortho.com</dd></div>
    </dl>
    <div class="shore" role="img" aria-label="Faint line illustration of waves, palm and sailboat along the shore"></div>
    <div class="seal">
      <div class="seal-core">
        <span class="mark-dot"></span>
        <span class="mark-name">Brindle Oaks</span>
      </div>
    </div>
  </section>

  <!-- Envelope: front -->
  <section class="piece envelope" aria-label="Envelope front">
    <svg class="flap" width="337" height="230" viewBox="0 0 337 230">
      <defs>
        <linearGradient id="flapGrad" x1="0" y1="0" x2="1" y2="0">
          <stop offset="0" stop-color="#2c57a3"/>
          <stop offset=".55" stop-color="#2f86b2"/>
          <stop offset="1" stop-color="#3fb7a0"/>
        </linearGradient>
      </defs>
      <polygon points="0,0 337,0 168.5,110" fill="url(#flapGrad)"/>
    </svg>
    <span class="sender-dot"></span>
    <div class="sender">
      <p class="firm">Brindle Oaks Orthodontics</p>
      <p class="doc">Doctor Name</p>
      <p class="addr">123 Street Name City, State Zip code</p>
      <p>office@brindleoaksortho.com</p>
      <p>www.brindleoaksortho.com</p>
    </div>
  </section>

  <!-- Envelope: back -->
  <section class="piece envelope-back" aria-label="Envelope back">
    <div class="face"></div>
    <div class="brand">
      <span class="mark-dot"></span>
      <span class="mark-name">Brindle Oaks</span>
    </div>
  </section>

  <!-- Letterhead -->
  <section class="piece letterhead" aria-label="Letterhead">
    <div class="coast-art" role="img" aria-label="Faint coastal illustration of waves, palm trees, sailboat and mermaids"></div>
    <div class="frame"></div>
    <div class="rule"></div>
    <div class="lh-brand">
      <span class="mark-dot"></span>
      <span class="mark-name">Brindle Oaks</span>
    </div>
    <address class="lh-contact" style="font-style:normal">
      <p class="doc">DOCTOR NAME</p>
      <p>123 Street Name</p>
      <p>City, State Zip code</p>
      <p>office@brindleoaksortho.com</p>
      <p>www.brindleoaksortho.com</p>
    </address>
  </section>

</body>
</html>
```